Norrell Advisory WA Business Card

Create an interesting, eye catching and colourful two sided business card. We are a business consulting operation assisting SME's improve all areas of their business. We provide consulting services to assist SME's to create a culture of continuous improvement, making a positive difference in the business. Our tag line is Small changes, big rewards. We want to create a well recognised, innovative brand that can be continued throughout our website, social media and email correspondence.

Target Market(s)

Small to Medium Enterprise Business Owners

Industry/Entity Type

Business Consultant

Contact Information for Business Card

Name of Business: Norrell Advisory - Small Changes Big Rewards
Derek Holloway Ph 0407385510 Megan Holloway Ph 0407913847
Email norrelladvisorywa@mailbox-example.com
Web address TBA
FaceBook page TBA

BACKSIDE OF CARD

Providing assistance with:

• Organisation & Efficiency
• Revenue generation & Marketing
• Financial Management
• Production quality & delivery
• Systems & Process documentation
• Exit Strategy

Font styles to use
Other font styles liked:
• Calibri

Colors

Designer to choose colors to be used in the design.

Requirements
Must have
• Calibri font

```html
<!DOCTYPE html>
<html lang="en">
<head>
<meta charset="utf-8">
<title>Norrell Advisory WA Business Card</title>
<link rel="stylesheet" href="https://fonts.googleapis.com/css2?family=Carlito:wght@400;700&display=swap">
<style>
  :root {
    --stage: #4a4a4c;
    --card: #ffffff;
    --brand-red: #e8412c;
    --brand-blue: #0b73b7;
    --ink: #1d1d1f;
    --paper-white: #ffffff;
  }
  * { box-sizing: border-box; margin: 0; padding: 0; }
  html, body {
    width: 1200px;
    height: 1000px;
    overflow: hidden;
    background: var(--stage);
    font-family: "Carlito", "Calibri", sans-serif;
  }
  .canvas { position: relative; width: 1200px; height: 1000px; }

  .card {
    position: absolute;
    left: 220px;
    width: 760px;
    height: 420px;
    background: var(--card);
    border-radius: 26px;
    overflow: hidden;
  }
  .card--back { top: 60px; }
  .card--front { top: 520px; }

  .brand {
    display: flex;
    align-items: center;
    gap: 12px;
    color: var(--brand-red);
    font-weight: 700;
    letter-spacing: 1px;
    text-transform: uppercase;
  }
  .brand__mark {
    width: 26px;
    height: 26px;
    background: var(--brand-red);
  }

  /* Back side */
  .card--back .brand {
    position: absolute;
    top: 120px;
    left: 0;
    right: 0;
    justify-content: center;
    font-size: 40px;
  }
  .card--back .brand__mark { width: 34px; height: 34px; }
  .mission {
    position: absolute;
    top: 222px;
    left: 0;
    right: 0;
    text-align: center;
    color: var(--brand-blue);
    font-weight: 700;
    font-size: 21px;
    letter-spacing: 0.5px;
  }
  .services {
    position: absolute;
    top: 262px;
    left: 0;
    right: 0;
    text-align: center;
    color: var(--ink);
    font-size: 19px;
    line-height: 1.45;
  }

  /* Front side */
  .card--front .brand {
    position: absolute;
    top: 112px;
    left: 40px;
    font-size: 34px;
  }
  .tagline {
    position: absolute;
    top: 158px;
    left: 42px;
    color: var(--ink);
    font-size: 16px;
    letter-spacing: 1px;
    text-transform: uppercase;
  }
  .contacts {
    position: absolute;
    top: 40px;
    right: 44px;
    text-align: left;
  }
  .contact { margin-bottom: 14px; }
  .contact__name {
    color: var(--brand-blue);
    font-weight: 700;
    font-size: 25px;
    letter-spacing: 0.5px;
    text-transform: uppercase;
  }
  .contact__phone {
    display: flex;
    align-items: center;
    gap: 6px;
    color: var(--ink);
    font-size: 24px;
  }
  .contact__phone svg { width: 18px; height: 18px; }

  .wave { position: absolute; left: 0; top: 0; width: 760px; height: 420px; }

  .links {
    position: absolute;
    right: 36px;
    bottom: 26px;
    list-style: none;
    text-align: right;
    color: var(--paper-white);
    font-size: 18px;
    line-height: 1.6;
  }
  .links li { display: flex; justify-content: flex-end; align-items: center; gap: 10px; }
  .links svg { width: 16px; height: 16px; }
</style>
</head>
<body>
<main class="canvas">

  <section class="card card--back" aria-label="Back of business card">
    <div class="brand"><span class="brand__mark"></span><span>Norrell Advisory</span></div>
    <p class="mission">CREATING A CULTURE OF CONTINUOUS IMPROVEMENT</p>
    <p class="services">
      Organisation &amp; Efficiency | Revenue generation &amp; Marketing | Financial Management<br>
      Production quality &amp; delivery | Systems &amp; Process documentation | Exit Strategy
    </p>
  </section>

  <section class="card card--front" aria-label="Front of business card">
    <svg class="wave" viewBox="0 0 760 420" aria-hidden="true">
      <path d="M0 214 C70 262 150 296 250 310 C150 290 70 254 0 234 Z" fill="var(--brand-red)"/>
      <path d="M0 256 C80 300 160 322 240 320 C330 318 420 270 520 250 C620 230 700 222 760 220 L760 420 L0 420 Z" fill="var(--brand-blue)"/>
    </svg>

    <div class="brand"><span class="brand__mark"></span><span>Norrell Advisory</span></div>
    <p class="tagline">Small changes * Big rewards</p>

    <div class="contacts">
      <div class="contact">
        <p class="contact__name">Derek Holloway</p>
        <p class="contact__phone">
          <svg viewBox="0 0 24 24" aria-hidden="true"><path d="M6.6 10.8a15 15 0 0 0 6.6 6.6l2.2-2.2a1 1 0 0 1 1-.25 11.4 11.4 0 0 0 3.6.57 1 1 0 0 1 1 1V20a1 1 0 0 1-1 1A17 17 0 0 1 3 4a1 1 0 0 1 1-1h3.5a1 1 0 0 1 1 1c0 1.25.2 2.45.57 3.57a1 1 0 0 1-.25 1z" fill="var(--brand-blue)"/></svg>
          0407385510
        </p>
      </div>
      <div class="contact">
        <p class="contact__name">Megan Holloway</p>
        <p class="contact__phone">
          <svg viewBox="0 0 24 24" aria-hidden="true"><path d="M6.6 10.8a15 15 0 0 0 6.6 6.6l2.2-2.2a1 1 0 0 1 1-.25 11.4 11.4 0 0 0 3.6.57 1 1 0 0 1 1 1V20a1 1 0 0 1-1 1A17 17 0 0 1 3 4a1 1 0 0 1 1-1h3.5a1 1 0 0 1 1 1c0 1.25.2 2.45.57 3.57a1 1 0 0 1-.25 1z" fill="var(--brand-blue)"/></svg>
          0407913847
        </p>
      </div>
    </div>

    <ul class="links">
      <li>norrelladvisorywa@mailbox-example.com
        <svg viewBox="0 0 16 16" aria-hidden="true"><rect x="1" y="3" width="14" height="10" rx="1" fill="var(--paper-white)"/><path d="M1.5 3.5 8 9l6.5-5.5" stroke="var(--brand-blue)" stroke-width="1.4" fill="none"/></svg>
      </li>
      <li>www.norrelladvisory-example.com
        <svg viewBox="0 0 16 16" aria-hidden="true"><circle cx="8" cy="8" r="6.5" fill="none" stroke="var(--paper-white)" stroke-width="1.5"/><path d="M1.5 8h13M8 1.5c-3 3.5-3 9.5 0 13M8 1.5c3 3.5 3 9.5 0 13" stroke="var(--paper-white)" stroke-width="1.2" fill="none"/></svg>
      </li>
      <li>norrelladvisory
        <svg viewBox="0 0 16 16" aria-hidden="true"><circle cx="8" cy="8" r="6.5" fill="var(--paper-white)"/></svg>
      </li>
    </ul>
  </section>

</main>
</body>
</html>
```